Vantro cards

I am in the auto motive, transportation business I would like a business card that is Something cool, modern edgy, having to do with car culture. I offer towing service for high and exotic cars. I also provide towing for collisions and car accidents. I offer open and enclosed transport nationwide.

Target Market(s)

Car culture people high end auto collectors

Industry/Entity Type

Towing car carrier

Contact Information for Business Card

My company colors black yellow and silver

Font styles to use
Serif

```html
<!DOCTYPE html>
<html lang="en">
<head>
<meta charset="utf-8">
<title>Vantro Transportation – Business Card</title>
<link href="https://fonts.googleapis.com/css2?family=Cinzel:wght@400;600;700&display=swap" rel="stylesheet">
<style>
  :root {
    --page-bg: #ebebeb;
    --card-bg: #d9d9d9;
    --ink: #111111;
    --navy: #1e2842;
    --slate: #3b4257;
    --yellow: #f2c300;
    --black: #0d0d0d;
  }
  * { box-sizing: border-box; margin: 0; padding: 0; }
  html, body {
    width: 1200px; height: 900px; overflow: hidden;
    background: var(--page-bg);
    font-family: "Cinzel", Georgia, serif;
  }
  .card {
    position: absolute; left: 100px; top: 162px;
    width: 1000px; height: 575px;
    background: var(--card-bg);
    box-shadow: 0 2px 6px rgba(0,0,0,0.12);
    overflow: hidden;
  }
  .brand {
    position: absolute; left: 64px; top: 222px; width: 320px;
    display: flex; align-items: flex-start; gap: 16px;
  }
  .brand-square {
    flex: 0 0 auto; width: 30px; height: 30px; margin-top: 8px;
    background: var(--yellow);
  }
  .brand-name {
    font-family: "Cinzel", Georgia, serif;
    font-weight: 700; font-size: 38px; line-height: 1.15;
    color: var(--ink);
  }
  .identity { position: absolute; left: 545px; top: 64px; }
  .person-name {
    font-size: 42px; font-weight: 600; color: var(--navy); line-height: 1;
  }
  .person-title {
    margin-top: 8px; font-size: 22px; font-weight: 400;
    color: var(--slate); letter-spacing: 1px; line-height: 1;
  }
  .rule {
    position: absolute; left: 545px; top: 157px;
    width: 350px; height: 3px; background: var(--black);
  }
  .rule::before {
    content: ""; position: absolute; left: 0; top: -1px;
    width: 85px; height: 6px; background: var(--yellow);
  }
  .contact-row {
    position: absolute; left: 470px; width: 510px; height: 54px;
    display: flex; align-items: center;
  }
  .contact-row.phone { top: 231px; }
  .contact-row.web { top: 320px; }
  .contact-row.address { top: 406px; }
  .contact-icon { width: 44px; height: 44px; flex: 0 0 auto; }
  .contact-divider {
    width: 2px; height: 46px; background: var(--black);
    margin-left: 30px; margin-right: 28px; flex: 0 0 auto;
  }
  .contact-text { color: var(--navy); line-height: 1.25; white-space: nowrap; }
  .phone .contact-text { font-size: 25px; font-weight: 700; }
  .web .contact-text { font-size: 23px; font-weight: 400; }
  .address .contact-text { font-size: 23px; font-weight: 600; }
  .hazard-band {
    position: absolute; left: 0; bottom: 0; width: 100%; height: 30px;
    background: linear-gradient(90deg, var(--yellow), #c9a200 50%, var(--yellow));
  }
</style>
</head>
<body>
  <div class="card">
    <div class="brand">
      <span class="brand-square"></span>
      <span class="brand-name">Vantro Transportation</span>
    </div>

    <div class="identity">
      <div class="person-name">Dorian Keller</div>
      <div class="person-title">Operation Manager</div>
    </div>
    <div class="rule"></div>

    <div class="contact-row phone">
      <svg class="contact-icon" viewBox="0 0 24 24" aria-hidden="true">
        <path fill="#111" d="M6.6 10.8c1.4 2.8 3.8 5.1 6.6 6.6l2.2-2.2c.3-.3.7-.4 1-.2 1.1.4 2.3.6 3.6.6.6 0 1 .4 1 1V20c0 .6-.4 1-1 1C10.6 21 3 13.4 3 4c0-.6.4-1 1-1h3.5c.6 0 1 .4 1 1 0 1.3.2 2.5.6 3.6.1.3 0 .7-.2 1L6.6 10.8z"/>
      </svg>
      <span class="contact-divider"></span>
      <div class="contact-text">+555-318-4072<br>+555-318-4096</div>
    </div>

    <div class="contact-row web">
      <svg class="contact-icon" viewBox="0 0 24 24" aria-hidden="true">
        <path fill="#111" d="M3 3l18 8.5-8 1.5-1.5 8z"/>
      </svg>
      <span class="contact-divider"></span>
      <div class="contact-text">hello@vantrotow.com<br>www.vantrotransport.com</div>
    </div>

    <div class="contact-row address">
      <svg class="contact-icon" viewBox="0 0 24 24" aria-hidden="true">
        <path fill="#111" d="M12 3L2 11.5h3V21h5v-6h4v6h5v-9.5h3z"/>
      </svg>
      <span class="contact-divider"></span>
      <div class="contact-text">418 Harbor Ln., Leon City,<br>4180 Leon</div>
    </div>

    <div class="hazard-band" role="img" aria-label="Decorative yellow and black hazard stripe band"></div>
  </div>
</body>
</html>
```